American cannabis tech company business card design

Pavrel.com is seeking a modern, professional, and brand-aligned business card that represents our company and its core values: Mission, Story, Values, and Impact. As an innovative cannabis company, we want a business card that is not only visually appealing but also serves as a representation of who we are and what we stand for.

Project Scope: Design a double-sided business card that integrates our brand identity and core values. Incorporate our key brand elements, ensuring a sleek and contemporary aesthetic. Visually reflect our core values (Mission, Story, Values, Impact) in a way that is engaging yet professional.

Target Market(s)

Vendors, third parties,

Contact Information for Business Card

Contact details (name, title, email, phone, website, etc.)

Font styles to use
Other font styles liked:
• Caslon, Centra

Colors

Designer to choose colors to be used in the design.

Requirements
Must have
• Pavrel.com logo and branding A creative yet clean way to integrate our core values (Mission, Story, Values, Impact) Modern typography and a well-structured layout
Nice to have
• forest green, grey, white, black
Should not have
• references to marijuana, leafs, plants, or related product

```html
<!DOCTYPE html>
<html lang="en">
<head>
<meta charset="utf-8">
<title>Pavrel.com Business Card</title>
<link href="https://fonts.googleapis.com/css2?family=Poppins:wght@400;700;800&display=swap" rel="stylesheet">
<style>
  :root {
    --forest: #1a3320;
    --forest-deep: #15301c;
    --forest-soft: #2f5738;
    --sage: #4f7a52;
    --paper: #ffffff;
    --paper-shade: #eeeeee;
    --ink-grey: #555a56;
    --rule: #9aa89c;
    --stage: #e6e7e4;
  }
  * { margin: 0; padding: 0; box-sizing: border-box; }
  html, body {
    width: 1200px; height: 900px; overflow: hidden;
    background: var(--stage);
    font-family: "Poppins", sans-serif;
  }
  .canvas {
    width: 1200px; height: 900px;
    display: flex; flex-direction: column;
    align-items: center; justify-content: center; gap: 56px;
  }
  .card {
    width: 580px; height: 331px;
    position: relative;
    box-shadow: 0 10px 26px rgba(0,0,0,0.18);
  }
  .card-front {
    background: var(--forest);
    border: 9px solid var(--sage);
    display: flex; align-items: center; justify-content: center;
  }
  .card-front .wordmark {
    font-weight: 800; font-size: 92px; letter-spacing: 2px;
    color: var(--forest-soft);
  }
  .card-back {
    background: linear-gradient(160deg, var(--paper) 40%, var(--paper-shade) 100%);
    border: 9px solid var(--forest);
  }
  .card-back .wordmark {
    position: absolute; top: 56px; left: 0; right: 0;
    text-align: center;
    font-weight: 800; font-size: 80px; letter-spacing: 2px; line-height: 1;
    color: var(--forest);
  }
  .details {
    position: absolute; left: 0; right: 0; top: 188px;
    display: flex; justify-content: center; align-items: stretch;
  }
  .person {
    text-align: right; padding-right: 18px;
    display: flex; flex-direction: column; justify-content: flex-end;
  }
  .person-name { font-weight: 700; font-size: 17px; color: var(--forest); line-height: 1.2; }
  .person-title { font-weight: 400; font-size: 16px; color: var(--ink-grey); line-height: 1.3; }
  .divider { width: 1px; background: var(--rule); }
  .contacts { list-style: none; padding-left: 16px; }
  .contacts li {
    display: flex; align-items: center; gap: 9px;
    font-size: 15px; color: var(--ink-grey); line-height: 1.75;
  }
  .contacts svg { width: 13px; height: 13px; fill: var(--forest); flex: none; }
</style>
</head>
<body>
<main class="canvas">
  <section class="card card-front">
    <span class="wordmark">PAVREL</span>
  </section>

  <section class="card card-back">
    <div class="wordmark">PAVREL</div>
    <div class="details">
      <div class="person">
        <div class="person-name">OWEN MARLOW</div>
        <div class="person-title">Co-founder &amp; CEO</div>
      </div>
      <div class="divider"></div>
      <ul class="contacts">
        <li>
          <svg viewBox="0 0 24 24" aria-hidden="true"><path d="M6.6 10.8a15.1 15.1 0 0 0 6.6 6.6l2.2-2.2a1 1 0 0 1 1-.25 11.4 11.4 0 0 0 3.6.57 1 1 0 0 1 1 1V20a1 1 0 0 1-1 1A17 17 0 0 1 3 4a1 1 0 0 1 1-1h3.5a1 1 0 0 1 1 1c0 1.25.2 2.45.57 3.6a1 1 0 0 1-.25 1z"/></svg>
          000-000-0000
        </li>
        <li>
          <svg viewBox="0 0 24 24" aria-hidden="true"><path d="M2 5h20v14H2z M3 6l9 7 9-7" stroke="#fff" stroke-width="1.5"/></svg>
          owen@pavrel.com
        </li>
        <li>
          <svg viewBox="0 0 24 24" aria-hidden="true"><circle cx="12" cy="12" r="10" fill="none" stroke="currentColor" stroke-width="2" style="stroke:var(--forest)"/><path d="M2 12h20M12 2c3 3 3 17 0 20M12 2c-3 3-3 17 0 20" fill="none" style="stroke:var(--forest)" stroke-width="1.6"/></svg>
          www.pavrel.com
        </li>
      </ul>
    </div>
  </section>
</main>
</body>
</html>
```